New Innovative Counselling and psychotherapy Service needs Business Card design

Keep it simple and professional. On one side, just company name and logo (perhaps in all blue) and maybe a tag line.

On other side (all white) my name and Qualifications in centre

Industry/Entity Type

Health And Wellness

Contact Information for Business Card

Dara Whelby
Counsellor & Psychotherapist
BSc (Psychol.), BA, Dip. (Couns. & Psych.), PG.Cert (CBT), FGTrK, ONRE

I will also require Mobile no, Email and web site address of which I'll pass on to final designer.

Font styles to use
Sans Serif

Requirements
Must have
• My Logo Only and please use the colours in logo that is in it.
Should not have
• Any other images

```html
<!DOCTYPE html>
<html lang="en">
<head>
<meta charset="utf-8">
<title>Harbour Lane – Business Card</title>
<link rel="stylesheet" href="https://fonts.googleapis.com/css2?family=Raleway:wght@400&family=Source+Sans+3:ital,wght@0,400;0,600;1,400&display=swap">
<style>
  :root {
    --backdrop: #6e6e6e;
    --card-white: #ffffff;
    --brand-blue: #45b2ec;
    --brand-green: #98d45c;
    --text-light: #ffffff;
    --text-dark: #333333;
    --text-tagline: #454545;
  }
  * { margin: 0; padding: 0; box-sizing: border-box; }
  html, body {
    width: 1200px;
    height: 802px;
    overflow: hidden;
    background: var(--backdrop);
  }
  .canvas {
    position: relative;
    width: 1200px;
    height: 802px;
  }
  .card {
    position: absolute;
    top: 274px;
    width: 442px;
    height: 265px;
    overflow: hidden;
  }

  /* Contact side */
  .card--contact {
    left: 136px;
    background: var(--brand-blue);
  }
  .card--contact .colour-band {
    position: absolute;
    left: 0; top: 0;
    width: 160px;
    height: 100%;
    background: var(--brand-green);
  }
  .contact-block {
    position: absolute;
    right: 26px;
    top: 94px;
    text-align: right;
    color: var(--text-light);
    font-family: "Source Sans 3", sans-serif;
    font-size: 12.5px;
    line-height: 16px;
  }
  .person-name {
    font-size: 17px;
    font-weight: 400;
    line-height: 19px;
    letter-spacing: 0.2px;
  }
  .person-role { margin-bottom: 1px; }
  .qualifications { font-style: italic; }
  .contact-list {
    list-style: none;
    margin-top: 20px;
  }
  .contact-list li {
    display: flex;
    justify-content: flex-end;
    align-items: center;
    gap: 3px;
  }
  .contact-icon { width: 10px; height: 10px; fill: var(--text-light); }

  /* Brand side */
  .card--brand {
    left: 624px;
    background: var(--card-white);
  }
  .brand-lockup {
    position: absolute;
    left: 97px;
    top: 104px;
    display: flex;
    align-items: center;
    gap: 14px;
  }
  .brand-dot {
    width: 46px;
    height: 46px;
    border-radius: 50%;
    background: var(--brand-blue);
  }
  .brand-name {
    font-family: "Raleway", sans-serif;
    font-weight: 400;
    font-size: 26px;
    color: var(--text-dark);
    letter-spacing: 0.2px;
  }
  .tagline {
    position: absolute;
    left: 0;
    right: 0;
    top: 223px;
    text-align: center;
    font-family: "Source Sans 3", sans-serif;
    font-weight: 600;
    font-size: 10.5px;
    letter-spacing: -0.2px;
    color: var(--text-tagline);
    text-transform: uppercase;
  }
</style>
</head>
<body>
<main class="canvas">

  <section class="card card--contact" aria-label="Business card, contact side">
    <div class="colour-band"></div>
    <div class="contact-block">
      <h1 class="person-name">DARA WHELBY</h1>
      <p class="person-role">Counsellor &amp; Psychotherapist</p>
      <p class="qualifications">BSc (Psychol.), BA<br>Dip. (Couns. &amp; Psych.),<br>PG.Cert (CBT), FGTrK, ONRE</p>
      <ul class="contact-list">
        <li>086 5520 917
          <svg class="contact-icon" viewBox="0 0 10 10" aria-hidden="true"><path d="M1 3.2C1 2 2.6 1.2 5 1.2S9 2 9 3.2v.8H7.2v-.9H2.8V4H1z M2.4 4.6h5.2L8.6 8.8H1.4z"/></svg>
        </li>
        <li>info@harbourlane.com
          <svg class="contact-icon" viewBox="0 0 10 10" aria-hidden="true"><path d="M0.5 2h9v6.5h-9z M1.2 2.6 5 5.6 8.8 2.6z" fill-rule="evenodd"/></svg>
        </li>
        <li>www.harbourlane.com
          <svg class="contact-icon" viewBox="0 0 10 10" aria-hidden="true"><circle cx="5" cy="5" r="4.5"/><path d="M3 3.5h2.5v2H4v2.3" stroke="#45b2ec" stroke-width="1" fill="none"/></svg>
        </li>
      </ul>
    </div>
  </section>

  <section class="card card--brand" aria-label="Business card, brand side">
    <div class="brand-lockup">
      <span class="brand-dot" aria-hidden="true"></span>
      <span class="brand-name">Harbour Lane</span>
    </div>
    <p class="tagline">Caring for your psychological well-being is our top priority</p>
  </section>

</main>
</body>
</html>
```